WP website design Kimbrell

We need a wordpress design that will incorporate a professional color scheme with company logo in a clean layout. The design needs to consider that this will be developed on a responsive theme. Colors are green of the logo, and tan and an accent color maybe black. Client wants a 'modern' look.

Industry/Entity Type

It Company

Font styles to use
Serif
Sans Serif

Colors

Requirements
Must have
• Must Have:
- Navigation: 1) Home; 2) Auctions; 3) Real Estate Listings 4) Mortgage Tips 5) Buying & Selling Tips 6) Sell A Farm 7) About Us 8) Contact Us

Site will have slideshow - image is attached. Colors will be those in the logo, tan and an accent color, maybe black.

Widgets: Featured Auctions, 2) Email signup form; 3) Testimonials widget; 4) Featured Properties; 5) Social Media (FB, linkedIn, RSS); 6) News & Events. Footer will have affiliation logo and contact info.

Home page content:
We are a family owned and operated business with over 25 years of real estate experience in Fairview and surrounding areas in the Western Plains. We know that purchasing a home is one of the most important decisions a person can make, and we strive to make it a successful and enjoyable experience for you!
Enjoy our website and please call if you have any questions or would like to make an appointment to view property!
Also, take a moment to look at our Auction Calendar for upcoming auction dates. Auctions are a great opportunity for great deals and rare finds, not to mention A LOT OF FUN!!

Widgets: 1) Featured Properties; 2) Call to action for Sellers 3) Testimonials blog/widget
Nice to have
• use of dropdown menus styling displayed - 1) Current Auctions & 2) Past Auctions under the Auctions link

```html
<!DOCTYPE html>
<html lang="en">
<head>
<meta charset="utf-8">
<title>Kimbrell Real Estate &amp; Auction Co.</title>
<link rel="stylesheet" href="https://fonts.googleapis.com/css2?family=Open+Sans:wght@400;600;700&family=Arimo:ital,wght@0,400;0,700;1,400&display=swap">
<style>
:root{
  --green:#0b4a14;
  --green-dark:#063a0c;
  --tan:#d4c99a;
  --tan-box:#d1b48a;
  --tan-light:#d9cf9f;
  --grey-box:#f0f0f0;
  --ink:#222;
  --black:#1b1b1b;
  --red:#cc1a1a;
  --white:#fff;
}
*{box-sizing:border-box;margin:0;padding:0}
html,body{width:878px;height:1200px;overflow:hidden}
body{position:relative;background:var(--tan);font-family:"Arimo",Arial,sans-serif;color:var(--ink)}
.page{position:absolute;left:102px;top:0;width:675px;height:1058px;background:var(--white)}
.abs{position:absolute}
.brand{left:108px;top:36px;display:flex;align-items:center;gap:8px;color:var(--green);font-family:"Open Sans",sans-serif;font-weight:600;font-size:16px;white-space:nowrap}
.brand .mark{width:14px;height:14px;background:var(--green)}
.social-label{left:496px;top:37px;font-family:"Open Sans",sans-serif;font-weight:700;font-size:15px;color:#444;letter-spacing:.5px}
.social{top:31px;width:30px;height:30px;border-radius:50%;background:#c9c9c9;border:2px solid #e4e4e4}
.nav{left:108px;top:81px;width:661px;height:33px;background:var(--green);display:flex;justify-content:space-around;align-items:center;border-radius:2px}
.nav a{color:var(--white);text-decoration:none;font-size:10px}
.dropdown{left:158px;top:114px;width:107px;border:1px solid #a89f75;font-size:10px}
.dropdown .item{height:26px;line-height:26px;padding-left:9px}
.dropdown .current{background:var(--tan-light);color:#222}
.dropdown .past{background:var(--green);color:var(--white)}
.hero{left:108px;top:119px;width:661px;height:259px;background:linear-gradient(180deg,#b9c3c9 0%,#9a4a3a 35%,#0f5a4c 55%,#7a3a2e 100%)}
.welcome-title{left:112px;top:406px;font-family:"Open Sans",sans-serif;font-weight:700;font-size:14.5px;color:var(--green)}
.welcome-text{left:113px;top:437px;width:410px;font-size:10.4px;line-height:13.6px}
.welcome-text p{margin-bottom:13.6px}
.cta{left:554px;top:398px;width:213px;height:41px;background:var(--green);color:var(--white);border-radius:3px;font-family:"Open Sans",sans-serif;font-weight:600;font-size:19px;text-align:center;line-height:41px}
.signup{left:553px;top:465px;width:213px;height:137px;background:var(--tan-box);padding:12px 16px}
.signup h3{font-family:"Open Sans",sans-serif;font-weight:700;font-size:15px;color:var(--black)}
.signup p{font-size:8.5px;line-height:12px;margin-top:4px}
.signup .field{margin-top:9px;width:166px;height:22px;background:var(--white);border:1px solid #ddd;font-size:8.5px;color:#888;padding-left:6px;line-height:20px}
.signup .btn{margin-top:13px;width:100px;height:23px;background:var(--green);color:var(--white);font-family:"Open Sans",sans-serif;font-weight:700;font-size:12px;text-align:center;line-height:23px}
.side-title{font-family:"Open Sans",sans-serif;font-weight:400;font-size:15px;color:var(--green);letter-spacing:.5px}
.listing{left:548px;top:658px;width:213px;height:172px;background:var(--grey-box);padding:10px 9px}
.listing h4{font-size:9px;font-weight:700;margin-left:3px}
.listing .photo{margin-top:8px;width:197px;height:79px;background:linear-gradient(180deg,#9fc4e4 0%,#8a2f24 55%,#4f7a33 100%)}
.listing .meta{font-size:8px;line-height:12px;margin:8px 0 0 3px}
.listing .note{font-size:9px;margin:6px 0 0 3px}
.testimonial{left:548px;top:875px;width:213px;height:168px;background:var(--grey-box);padding:12px 10px 0 11px}
.testimonial .quote{font-style:italic;font-size:8.6px;line-height:13.6px;color:#555}
.testimonial .by{position:absolute;right:62px;top:135px;text-align:right;font-style:italic;font-size:7.5px;line-height:11px}
.testimonial .by .date{color:var(--red)}
.testimonial .avatar{position:absolute;right:13px;top:127px;width:38px;height:33px;background:linear-gradient(180deg,#6b5a48,#c9a98a)}
.auction{left:112px;width:416px;height:189px;background:var(--grey-box)}
.auction .photo{position:absolute;left:9px;top:12px;width:154px;height:129px;background:linear-gradient(180deg,#6fa2d8 0%,#e9ddcb 45%,#c2b39c 75%,#7d7b72 100%)}
.auction .btn{position:absolute;top:152px;height:21px;color:var(--white);font-size:10px;line-height:21px;padding-left:22px}
.auction .btn svg{position:absolute;left:7px;top:5px}
.auction .details{left:9px;width:66px;background:var(--black)}
.auction .gallery{left:90px;width:73px;background:var(--green)}
.panel{position:absolute;left:174px;width:232px;background:var(--white);border:1px solid #e0e0e0;padding:6px 7px}
.panel h5{font-weight:400;font-size:10px;color:var(--green)}
.auction.alt .panel h5{color:var(--red)}
.panel p{font-size:8.3px;line-height:13px;margin-top:3px}
.panel .small{font-size:7.4px;line-height:11px}
.panel .label{font-weight:700;font-size:8px;margin-top:8px}
.footer{left:0;top:1058px;width:878px;height:114px;background:var(--green-dark)}
.footer-info{left:112px;top:1090px;color:var(--white);font-size:8.8px;line-height:12.1px}
.footer-brand{left:604px;top:1108px;display:flex;align-items:center;gap:8px;color:#dfe6dc;font-family:"Open Sans",sans-serif;font-weight:600;font-size:15px;white-space:nowrap}
.footer-brand .mark{width:13px;height:13px;background:#dfe6dc}
.copyright{left:0;top:1172px;width:878px;height:28px;background:var(--black);color:#eee;font-size:8.6px;text-align:center;line-height:28px}
</style>
</head>
<body>
<div class="page"></div>

<header>
  <div class="abs brand"><span class="mark"></span>Kimbrell Real Estate &amp; Auction Co.</div>
  <div class="abs social-label">SOCIAL MEDIA:</div>
  <span class="abs social" style="left:635px" role="img" aria-label="Social link one"></span>
  <span class="abs social" style="left:675px" role="img" aria-label="Social link two"></span>
  <span class="abs social" style="left:715px" role="img" aria-label="News feed link"></span>
  <nav class="abs nav">
    <a href="#">Home</a><a href="#">Auctions</a><a href="#">Real Estate Listings</a><a href="#">Mortgage Tips</a><a href="#">Buying &amp; Selling Tips</a><a href="#">Sell A Farm</a><a href="#">About Us</a><a href="#">Contact Us</a>
  </nav>
</header>

<div class="abs hero" role="img" aria-label="Slideshow photo of the red brick company storefront with green awnings"></div>
<div class="abs dropdown"><div class="item current">Current Auctions</div><div class="item past">Past Auctions</div></div>

<h1 class="abs welcome-title">WELCOME TO KIMBRELL REAL ESTATE</h1>
<div class="abs welcome-text">
  <p>We are a family owned and operated business with over 25 years of real estate experience in Fairview and surrounding areas in the Western Plains. We know that purchasing a home is one of the most important decisions a person can make, and we strive to make it a successful and enjoyable experience for you!</p>
  <p>Enjoy our website and please call if you have any questions or would like to make an appointment to view property!</p>
  <p>Also, take a moment to look at our Auction Calendar for upcoming auction dates. Auctions are a great opportunity for great deals and rare finds, not to mention A LOT OF FUN!!</p>
</div>

<section class="abs auction" style="top:622px">
  <div class="photo" role="img" aria-label="Photo of a two-storey stucco house with red shutters"></div>
  <div class="btn details"><svg width="10" height="10" viewBox="0 0 10 10"><circle cx="4" cy="4" r="3" fill="none" stroke="#fff" stroke-width="1.5"/><line x1="6" y1="6" x2="9" y2="9" stroke="#fff" stroke-width="1.5"/></svg>Details</div>
  <div class="btn gallery"><svg width="12" height="10" viewBox="0 0 12 10"><rect x="0.5" y="0.5" width="8" height="6" fill="none" stroke="#fff"/><rect x="3.5" y="3.5" width="8" height="6" fill="none" stroke="#fff"/></svg>Gallery</div>
  <div class="panel" style="top:11px;height:62px"><h5>Auction 1</h5><p>Lorem Ipsum is simply dummy text of the printing and typesetting industry.</p></div>
  <div class="panel" style="top:85px;height:96px"><h5>Online Bidding Only</h5><p class="small">Began:&nbsp; Friday, May 24, 2013 at 10:06 AM EDT</p><p class="label">Location</p><p class="small" style="margin-top:0">1820 Maple Ln. NW Oak Ridge, IA 52400</p><p style="line-height:12px">Harlow tractor w/Beck Loader, Dune Cutditioner: SHOP &amp; MISCELLANIOUS &amp; PORK .</p></div>
</section>

<section class="abs auction alt" style="top:854px">
  <div class="photo" role="img" aria-label="Photo of a two-storey stucco house with red shutters"></div>
  <div class="btn details"><svg width="10" height="10" viewBox="0 0 10 10"><circle cx="4" cy="4" r="3" fill="none" stroke="#fff" stroke-width="1.5"/><line x1="6" y1="6" x2="9" y2="9" stroke="#fff" stroke-width="1.5"/></svg>Details</div>
  <div class="btn gallery"><svg width="12" height="10" viewBox="0 0 12 10"><rect x="0.5" y="0.5" width="8" height="6" fill="none" stroke="#fff"/><rect x="3.5" y="3.5" width="8" height="6" fill="none" stroke="#fff"/></svg>Gallery</div>
  <div class="panel" style="top:11px;height:62px"><h5>Auction 1</h5><p>Lorem Ipsum is simply dummy text of the printing and typesetting industry.</p></div>
  <div class="panel" style="top:85px;height:96px"><h5>Online Bidding Only</h5><p class="small">Began:&nbsp; Friday, May 24, 2013 at 10:06 AM EDT</p><p class="label">Location</p><p class="small" style="margin-top:0">1820 Maple Ln. NW Oak Ridge, IA 52400</p><p style="line-height:12px">Harlow tractor w/Beck Loader, Dune Cutditioner: SHOP &amp; MISCELLANIOUS &amp; PORK .</p></div>
</section>

<aside>
  <div class="abs cta">Seller your Property</div>
  <div class="abs signup">
    <h3>EMAIL SIGN UP</h3>
    <p>Lorem Ipsum is simply dummy text of the printing and typesetting industry.</p>
    <div class="field">Enter your Email Address</div>
    <div class="btn">SUBSCRIBE</div>
  </div>
  <h2 class="abs side-title" style="left:549px;top:629px">FEATURED LISTINGS</h2>
  <div class="abs listing">
    <h4>Multi Estate &amp; Consignment Auction</h4>
    <div class="photo" role="img" aria-label="Photo of a red brick family home with a green lawn"></div>
    <div class="meta"><b>Start Date/ Time:</b> Saturday, April 13,<br>2013 At 10:00 Am</div>
    <div class="note">Multi Estate &amp; Consignment Auction</div>
  </div>
  <h2 class="abs side-title" style="left:555px;top:848px">TESTIMONIALS</h2>
  <div class="abs testimonial">
    <p class="quote">&ldquo; Lorem Ipsum has been the industry's standard dummy text ever since the 1500s, when an unknown printer took a galley of type and scrambled it to make a type speci men book.It has survived not only five centuries, but also the leap into electronic typesetting, remaining essentially unchanged.</p>
    <div class="by"><div>Dana Whitfield</div><div class="date">Posted on Nov25, 2013</div></div>
    <div class="avatar" role="img" aria-label="Portrait of the reviewer"></div>
  </div>
</aside>

<footer>
  <div class="abs footer"></div>
  <div class="abs footer-info">KIMBRELL Real Estate &amp; Auction Company LLC<br>Daniel Kimbrell<br>410 Main Street, P.O. Box 218<br>Fairview, IL 62500<br>Phone 555-014-2290 or 1-800-555-0163<br>dkimbrell@kimbrellauctions.com</div>
  <div class="abs footer-brand"><span class="mark"></span>Kimbrell Real Estate &amp; Auction Co.</div>
  <div class="abs copyright">Copyright © 2014 Kimbrell Real Estate All Rights Reserved.</div>
</footer>
</body>
</html>
```